4 panel (or page) brochure

We need a brochure design for a Oklahoma based company. We manufacture and sell underground and below ground shelters. We sell our shelters in our local showroom, as well distribute our shelters to a big box national retailer. I would like to have a simple design that includes a few pictures of our product and details on each product we offer as well as install details for each product. Our out of state retailers likely will not have our product display so we will need something that sells the product without seeing it in person.

I would like something that it easily printable as well as able to edit at a later time if needed.

I've included Catalog/Brochure Copy
Pictures of Below Ground Units/Above Ground Units - feel free to edit or touch up.
Some brochure ideas I found on Draftwell that seemed to be similar to what we can do.
The Inside of a brochure we did a while back that we liked (style-wise)
A general info flyer for more information

It Company

```html
<!DOCTYPE html>
<html lang="en">
<head>
<meta charset="utf-8">
<title>StormHaven Shelters Brochure</title>
<link href="https://fonts.googleapis.com/css2?family=Montserrat:wght@400;600;700;800&family=Open+Sans:wght@400;600&display=swap" rel="stylesheet">
<style>
:root{
  --red:#d0202a;
  --red-dark:#a8161f;
  --ink:#3a3a3a;
  --muted:#6b6b6b;
  --paper:#ffffff;
  --stage:#e9e9e9;
  --line:#d9d9d9;
  --storm-dark:#2b2d30;
  --storm-mid:#6d7075;
  --storm-light:#b9bcc0;
  --table-head:#8d8d8d;
  --table-row:#efefef;
}
*{box-sizing:border-box;margin:0;padding:0}
html,body{width:1200px;height:900px;overflow:hidden}
body{background:var(--stage);font-family:"Open Sans",Arial,sans-serif;color:var(--ink);position:relative}
.page{position:absolute;background:var(--paper);overflow:hidden}
.photo{position:absolute}
.storm{background:linear-gradient(160deg,var(--storm-light),var(--storm-mid) 55%,var(--storm-dark))}
.concrete{background:linear-gradient(135deg,#c9cbcd,#8e9194 60%,#b8babd)}
.family{background:linear-gradient(180deg,#f4f4f4,#e2dcd6)}
.door{background:linear-gradient(90deg,#f6f6f6,#d6d6d6)}
.brand{position:absolute;display:flex;align-items:center;gap:5px;font-family:"Montserrat",sans-serif;font-weight:800;color:var(--red);letter-spacing:.5px}
.brand .dot{width:10px;height:10px;border-radius:50%;background:var(--red)}

/* cover */
.cover{left:30px;top:195px;width:370px;height:510px}
.cover .swirl{position:absolute;left:0;top:0;width:370px;height:175px;background:radial-gradient(ellipse at 20% 40%,#f1f1f1,#fff 70%)}
.cover .brand{left:215px;top:95px;font-size:15px}
.cover-band{position:absolute;left:0;top:410px;width:370px;height:100px;background:var(--red);display:flex;align-items:center;padding:0 16px;gap:12px;color:#fff;font-family:"Montserrat",sans-serif}
.cover-band .lead{font-size:8px;line-height:1.35;text-transform:uppercase;letter-spacing:.6px;width:120px;font-weight:400}
.cover-band .claim{font-size:22px;font-weight:800;letter-spacing:.5px}

/* spread */
.spread{left:430px;top:195px;width:740px;height:510px}
.spread .fold{position:absolute;left:370px;top:0;width:1px;height:510px;background:rgba(0,0,0,.08)}
.hero{left:0;top:0;width:740px;height:150px;background:linear-gradient(100deg,#d8d9db,#7a7d82 40%,#26282b 75%,#1c1d1f)}
.hero-copy{position:absolute;left:395px;top:14px;width:330px;color:#fff}
.hero-copy .brand{position:static;justify-content:flex-end;font-size:9px;color:#fff}
.hero-copy h1{font-family:"Montserrat",sans-serif;font-size:15px;font-weight:700;letter-spacing:.5px;margin:10px 0 6px}
.cols{display:flex;gap:12px;font-size:4.6px;line-height:1.45;color:#e6e6e6}
.cols p{flex:1}
.cols p+p{margin:0}

.section-band{position:absolute;left:0;top:150px;width:335px;height:34px;background:var(--red);clip-path:polygon(0 0,100% 0,92% 100%,0 100%);display:flex;align-items:center;padding-left:190px;gap:6px;color:#fff;font-family:"Montserrat",sans-serif}
.section-band .mark{width:7px;height:7px;background:#fff}
.section-band h2{font-size:9px;line-height:1.05;font-weight:700;letter-spacing:.4px}
.section-band h2 span{display:block;font-weight:400}

.garage-photo{left:20px;top:198px;width:150px;height:88px}
.intro{position:absolute;left:182px;top:200px;width:172px;font-size:4.8px;line-height:1.5;color:var(--muted)}
.intro p+p{margin-top:4px}
h3{font-family:"Montserrat",sans-serif;font-size:5.4px;font-weight:700;color:var(--red);text-transform:uppercase;letter-spacing:.3px;margin-bottom:3px}
.sizes{position:absolute;left:20px;top:296px;width:155px}
.sizes table{width:100%;border-collapse:collapse;font-size:4.6px}
.sizes th{background:var(--table-head);color:#fff;font-weight:600;padding:3px}
.sizes td{padding:4px 3px;border-bottom:1px solid #fff;background:var(--table-row);text-align:center}
.sizes td:first-child{text-align:left;font-weight:600}
.sizes .notes{margin-top:8px;font-size:4.6px;line-height:1.5;color:var(--muted);list-style:none}
.features{position:absolute;left:185px;top:296px;width:170px;font-size:4.6px;line-height:1.55;color:var(--muted)}
.features ul{list-style:none;margin-bottom:7px}
.features li::before{content:"• ";color:var(--ink)}

/* right page */
.install{position:absolute;left:380px;top:163px;width:152px;height:333px;border:1px solid var(--red);border-radius:6px;padding:6px}
.steps{display:grid;grid-template-columns:1fr 1fr;gap:4px 5px;margin-top:3px}
.step{font-size:4.2px;line-height:1.3;color:var(--muted)}
.step .shot{height:40px;margin-bottom:2px;background:linear-gradient(135deg,#b7b2aa,#6f6a64)}
.step:first-child{grid-column:1/3}
.step:first-child .shot{display:none}
.install .footnote{font-size:4.2px;color:var(--muted);margin-top:5px;font-style:italic}
.side{position:absolute;left:542px;top:166px;width:185px;font-size:4.6px;line-height:1.5;color:var(--muted)}
.side ul{list-style:none;margin-bottom:4px}
.side li::before{content:"• ";color:var(--ink)}
.side .note{font-weight:600;color:var(--ink);font-style:italic;margin-bottom:8px}
.faq dt{font-weight:600;color:var(--ink);margin-top:4px}
.faq dd{margin-left:5px}
</style>
</head>
<body>

<section class="page cover" aria-label="Brochure cover">
  <div class="swirl"></div>
  <div class="brand"><span class="dot"></span>StormHaven</div>
  <div class="photo storm" style="left:0;top:175px;width:120px;height:235px" role="img" aria-label="Tornado over an empty highway"></div>
  <div class="photo concrete" style="left:120px;top:135px;width:250px;height:140px" role="img" aria-label="Open in-ground shelter hatch set in a concrete floor"></div>
  <div class="photo family" style="left:110px;top:275px;width:190px;height:135px" role="img" aria-label="Smiling family of four dressed in white"></div>
  <div class="photo door" style="left:300px;top:275px;width:70px;height:135px" role="img" aria-label="White above-ground safe room with open door"></div>
  <div class="cover-band">
    <p class="lead">Be prepared and provide your family with</p>
    <p class="claim">PEACE OF MIND</p>
  </div>
</section>

<section class="page spread" aria-label="Brochure inside spread">
  <div class="photo hero" role="img" aria-label="Dark storm clouds with a tornado and lightning"></div>
  <div class="fold"></div>

  <div class="hero-copy">
    <div class="brand"><span class="dot"></span>StormHaven</div>
    <h1>DON'T LEAVE LIFE TO CHANCES</h1>
    <div class="cols">
      <p>StormHaven is dedicated to quality and experience, working with our design and manufacturing partners to build the best shelters in the industry. We have installed thousands of storm shelters and have an approach that keeps quality high at an affordable price. Each storm shelter is built to the highest quality standards and tested to federal guidelines by Plainsview University's wind science and engineering research center.</p>
      <p>Protect yourself from the 250 mph winds of an EF5 tornado with our time-tested, proven shelter design. StormHaven is an Redbud City based company. We manufacture shelters in our own plant and service the whole region. Our team has spent a decade of experience in manufacturing and installing storm shelters, and we take pride in the product and service we provide to our customers, from the sale process, to installation, to assistance after the sale.</p>
    </div>
  </div>

  <div class="section-band">
    <span class="mark"></span>
    <h2>IN-GROUND<span>GARAGE SHELTERS</span></h2>
  </div>

  <div class="photo concrete garage-photo" role="img" aria-label="Garage shelter with sliding lid set flush in the floor"></div>
  <div class="intro">
    <p>Convenience is key when it comes to safety during a storm. StormHaven shelters are out of the weather and out of harm's way. Our storm shelters are unique because they can be installed in your garage and don't require the use of valuable square footage. Our shelter design allows access to your shelter while your vehicle is parked, providing your family with a quick and safe place to ride out any life-threatening storm. Pulling the vehicle all the way forward in a standard size garage will provide room to enter the shelter while the vehicle remains parked over it. Installation typically takes between 6-8 hours depending on the size of your shelter.</p>
  </div>

  <div class="sizes">
    <h3>Types &amp; Sizes</h3>
    <table>
      <tr><th>Type</th><th>Size</th><th>Fits</th></tr>
      <tr><td>Small</td><td>3'(W) × 7'(L) × 4'(H)</td><td>6-8 people</td></tr>
      <tr><td>Medium</td><td>3'(W) × 9'(L) × 4'(H)</td><td>8-12 people</td></tr>
      <tr><td>Large</td><td>3'(W) × 11'(L) × 4'(H)</td><td>12-16 people</td></tr>
      <tr><td>XL</td><td>3'(W) × 13'(L) × 4'(H)</td><td>16+ people</td></tr>
    </table>
    <ul class="notes">
      <li>Meets federal guidelines for storm shelters</li>
      <li>Meets national guidelines for storm shelters</li>
      <li>Tested by Plainsview University</li>
      <li>Member of Regional Shelter Alliance</li>
    </ul>
  </div>

  <div class="features">
    <h3>Technical Features</h3>
    <ul>
      <li>Completely flush with the concrete floor</li>
      <li>Outside surface coated with sealant epoxy to prevent rust</li>
      <li>Plate and sliding lid are 1/4" thick steel</li>
      <li>10-gauge steel surrounding walls</li>
      <li>Welds are dense tested for quality control</li>
      <li>Self-locking door design for security</li>
      <li>Air ventilated</li>
      <li>Emergency secondary lid exit</li>
      <li>Carpeted steps and benches</li>
      <li>Steps are removable to allow more room in your shelter</li>
      <li>Lifetime non-transferable warranty against leaking and floating</li>
    </ul>
    <h3>Additional Benefits</h3>
    <ul>
      <li>Maintains existing square footage</li>
      <li>Can be installed in existing structures as well as new construction</li>
      <li>Car can be parked on surrounding concrete, allowing access to your shelter</li>
    </ul>
  </div>

  <div class="install">
    <h3>Installation Process</h3>
    <div class="steps">
      <div class="step"><span class="shot"></span>1. Measure and cut concrete to installation size</div>
      <div class="step"><span class="shot" role="img" aria-label="Concrete cut in garage floor"></span>2. Test saw concrete from slab removal</div>
      <div class="step"><span class="shot" role="img" aria-label="Excavation of the pit"></span>3. Excavate the dirt out of the hole</div>
      <div class="step"><span class="shot" role="img" aria-label="Shelter lowered into the hole"></span>4. Lower the shelter into place and level</div>
      <div class="step"><span class="shot" role="img" aria-label="Rebar placed around the shelter"></span>5. Reinforce with rebar</div>
      <div class="step"><span class="shot" role="img" aria-label="Concrete poured around the unit"></span>6. Backfill with concrete to hold the shelter in place</div>
      <div class="step"><span class="shot" role="img" aria-label="Top layer of concrete finished"></span>7. Top with 12 inches of concrete and level</div>
      <div class="step"><span class="shot" role="img" aria-label="Shelter area cleaned"></span>8. Area is cleaned with power washer</div>
      <div class="step"><span class="shot" role="img" aria-label="Finished flush shelter lid"></span>9. Smooth and set</div>
    </div>
    <p class="footnote">Typically installed within 6-8 hours</p>
  </div>

  <div class="side">
    <h3>Customization &amp; Upgrades</h3>
    <ul>
      <li>Metal steps &amp; benches: $150</li>
      <li>6" wide escape, carpeted steps: $600 (standard size 6')</li>
      <li>12" wide escape, carpeted stepped size: $900</li>
      <li>Color matched: $50</li>
      <li>Hole formed for lights: $75</li>
      <li>Outside vent kit: $120</li>
    </ul>
    <p class="note">An as-upgrade our in-ground shelters can also be installed outside with our specially designed outside kit. Ask about the outside kit upgrade pricing.</p>
    <h3>FAQ</h3>
    <dl class="faq">
      <dt>1. Can I park on my below-ground shelter?</dt>
      <dd>Yes, you can park on our shelters. Our shelters have been designed to be durable and can withstand the weight of your vehicle. We do recommend parking in a way where you can still enter the shelter.</dd>
      <dt>2. Can I get trapped in my shelter?</dt>
      <dd>Our locking mechanism is simple yet sturdy and secure. The opening system is designed to slide open even with debris on top. If something did cover the lid, the shelter has a secondary exit, and a rescue crew can pry the lid open from the outside of the unit.</dd>
      <dt>3. Will there be a mess?</dt>
      <dd>We cover all of the floor and walls near the install. After the install is complete we power wash the work area as well as the driveway in most cases, and the area is cleaner than when we arrive.</dd>
      <dt>4. Will the shelter look flat once it's installed?</dt>
      <dd>Yes, the shelter will actually stand 1/8 of an inch over the original slab to prevent water from going into the shelter. However, our concrete experts will grade the concrete around the slab so that it looks flat. This allows water to run away from the shelter.</dd>
    </dl>
  </div>
</section>

</body>
</html>
```